Fresh new and cool frozen burger box! Come be a part of an amazing project!

Crust Drums and Melts restaurant is expanding into the frozen foods market!
please check out our website to understand the vibe of the company
https://crumbvale.ca
this is a line of premium Halal meat, we want to stress our top-notch quality.
we like the orange colours so see what you can do with them. (maybe white and orange combo)
you have lots of creative freedom here, feel free to use the burger photo I am attaching or any image off the website.
logo should be nice and visible.
we want this packaging to really stand out and be special.
Come be a part of an amazing project!
Muslim Flails, looking of a quality meat burger. mostly already familiar with our brand
Frozen food

```html
<!DOCTYPE html>
<html lang="en">
<head>
<meta charset="utf-8">
<title>Crumbvale Premium Beef Burgers – Box Panels</title>
<link rel="stylesheet" href="https://fonts.googleapis.com/css2?family=Anton&family=Alfa+Slab+One&family=Kaushan+Script&family=Roboto+Condensed:wght@400;700&family=Arimo:wght@400;700&display=swap">
<style>
  :root {
    --orange: #f39122;
    --orange-deep: #e07f12;
    --wood: #2a2a2a;
    --wood-dark: #1b1b1b;
    --wood-light: #3a3a3a;
    --white: #ffffff;
    --paper: #f0f0f0;
    --red: #e0242b;
    --ink: #111111;
    --photo-warm: #d9a05c;
    --photo-deep: #8a4a24;
  }
  * { box-sizing: border-box; margin: 0; padding: 0; }
  html, body { width: 822px; height: 1200px; overflow: hidden; }
  body { background: var(--paper); position: relative; font-family: "Roboto Condensed", sans-serif; }

  .panel { position: absolute; overflow: hidden; }
  .wood {
    background:
      repeating-linear-gradient(90deg, rgba(255,255,255,0.03) 0 2px, transparent 2px 38px),
      linear-gradient(180deg, var(--wood-light), var(--wood) 45%, var(--wood-dark));
  }

  /* ---------- Lid panel ---------- */
  .lid { left: 31px; top: 50px; width: 760px; height: 280px; }
  .lid-band {
    position: absolute; left: 60px; top: 0; width: 120px; height: 100%;
    background: var(--orange);
  }
  .lid-band::after {
    content: ""; position: absolute; inset: 0 10px; border-left: 1.5px solid var(--white); border-right: 1.5px solid var(--white);
  }
  .lid-brand {
    position: absolute; left: 50%; top: 50%;
    transform: translate(-50%, -50%) rotate(90deg);
    text-align: center; white-space: nowrap;
  }
  .lid-brand .brand-name { font-family: "Anton", sans-serif; font-size: 44px; color: var(--white); letter-spacing: 1px; line-height: 1; }
  .lid-brand .brand-tag { font-size: 14px; font-weight: 700; color: var(--ink); }

  .label {
    position: absolute; left: 215px; top: 18px; width: 525px; height: 200px;
    background: var(--white); padding: 12px 14px;
  }
  .claim { position: absolute; left: 14px; top: 12px; width: 200px; line-height: 0.95; }
  .claim-top, .claim-bottom { font-family: "Anton", sans-serif; color: var(--orange); font-size: 24px; letter-spacing: 0.5px; }
  .claim-bottom { font-size: 32px; }
  .claim-script { font-family: "Kaushan Script", cursive; color: var(--red); font-size: 22px; display: block; margin: -4px 0 -2px 14px; }

  .nutrition {
    position: absolute; left: 14px; top: 100px; width: 310px;
    border: 1px solid var(--ink); font-family: "Arimo", sans-serif; font-size: 5.5px; color: var(--ink);
    display: grid; grid-template-columns: 115px 1fr; line-height: 1.25;
  }
  .nutrition-head { padding: 2px 3px; border-right: 1px solid var(--ink); }
  .nutrition-head h3 { font-size: 11px; line-height: 1; }
  .nutrition-table { border-collapse: collapse; width: 100%; }
  .nutrition-table td { border-bottom: 0.6px solid var(--ink); padding: 0 3px; }
  .nutrition-table tr:last-child td { border-bottom: none; }
  .nutrition-table td:last-child { text-align: right; }

  .ingredients {
    position: absolute; right: 14px; top: 12px; width: 180px;
    border: 1.5px solid var(--orange); padding: 4px 8px;
    font-family: "Arimo", sans-serif; font-weight: 700; font-size: 7px; line-height: 1.2; color: var(--ink);
  }
  .ingredients h4 { color: var(--red); font-size: 7px; margin-bottom: 2px; }
  .maker-lines { position: absolute; right: 110px; top: 110px; font-family: "Arimo", sans-serif; font-size: 5.5px; font-weight: 700; color: var(--ink); line-height: 2.4; }

  /* ---------- Front panel ---------- */
  .front { left: 31px; top: 360px; width: 760px; height: 300px; }
  .ribbon {
    position: absolute; left: 40px; top: 0; width: 100px; height: 270px;
    background: var(--orange);
    clip-path: polygon(0 0, 100% 0, 100% 100%, 50% 90%, 0 100%);
  }
  .ribbon-frame {
    position: absolute; left: 7px; top: 0; width: 86px; height: 250px;
    border: 1.5px solid var(--white); border-top: none;
    clip-path: polygon(0 0, 100% 0, 100% 100%, 50% 88%, 0 100%);
  }
  .ribbon-seal {
    position: absolute; left: 22px; top: 130px; width: 56px; height: 56px;
    border: 2px solid var(--white); border-radius: 50%;
  }

  .front-brand { position: absolute; left: 190px; top: 30px; }
  .front-brand .brand-name { font-family: "Anton", sans-serif; font-size: 50px; color: var(--orange); line-height: 1; display: flex; align-items: center; gap: 10px; }
  .brand-dot { width: 34px; height: 34px; border-radius: 50%; background: var(--white); display: inline-block; }
  .front-brand .brand-tag { font-size: 17px; font-weight: 700; color: var(--white); margin-top: 4px; letter-spacing: 0.5px; }
  .sep { color: var(--red); }

  .burger-photo {
    position: absolute; left: 200px; top: 130px; width: 230px; height: 150px;
    border-radius: 12px;
    background: radial-gradient(ellipse at 50% 45%, var(--photo-warm) 0%, var(--photo-deep) 100%);
  }

  .product-title { position: absolute; left: 480px; top: 34px; width: 250px; text-align: center; }
  .premium-banner {
    display: inline-block; border: 2px solid var(--orange); padding: 4px 16px;
    font-family: "Alfa Slab One", serif; font-size: 24px; color: var(--white); letter-spacing: 1px;
  }
  .product-beef, .product-burgers { font-family: "Anton", sans-serif; line-height: 1; letter-spacing: 1px; }
  .product-beef { font-size: 58px; color: var(--white); }
  .product-burgers { font-size: 58px; color: var(--orange); }

  .chalk-rule { position: absolute; left: 505px; top: 236px; width: 220px; height: 2px; background: var(--white); opacity: 0.85; }
  .contact { position: absolute; left: 505px; top: 252px; display: flex; align-items: center; gap: 7px; }
  .contact-dot { width: 18px; height: 18px; border-radius: 50%; background: var(--orange); }
  .contact-globe { width: 18px; height: 18px; }
  .contact-url { font-family: "Alfa Slab One", serif; color: var(--orange); font-size: 17px; margin-left: 6px; }

  /* ---------- End panels ---------- */
  .end { top: 700px; width: 370px; height: 300px; background: var(--orange); }
  .end-left { left: 31px; }
  .end-right { left: 421px; }
  .end-title { position: absolute; left: 0; right: 0; top: 40px; text-align: center; color: var(--white); }
  .end-title .premium-banner { border-color: var(--white); font-size: 20px; }
  .end-title .product-beef, .end-title .product-burgers { color: var(--white); font-size: 50px; }
  .end-brand { position: absolute; left: 0; right: 0; bottom: 26px; text-align: center; }
  .end-brand .brand-name { font-family: "Anton", sans-serif; font-size: 26px; color: var(--ink); line-height: 1; }
  .end-brand .brand-tag { font-size: 11px; font-weight: 700; color: var(--ink); }
</style>
</head>
<body>

  <!-- Lid -->
  <section class="panel lid wood">
    <div class="lid-band">
      <div class="lid-brand">
        <div class="brand-name">CRUMBVALE</div>
        <div class="brand-tag">Crust <span class="sep">•</span> Drums <span class="sep">•</span> Melts</div>
      </div>
    </div>

    <div class="label">
      <div class="claim">
        <div class="claim-top">MIGHT JUST BE</div>
        <span class="claim-script">the best burger</span>
        <div class="claim-bottom">ON EARTH</div>
      </div>

      <div class="nutrition">
        <div class="nutrition-head">
          <h3>Nutrition Facts</h3>
          <p>Serving Size 1 Meal</p>
          <p>Servings Per Container 1</p>
          <p><b>Calories 450</b> Calories from Fat 200</p>
          <p>*Percent Daily Values are based on a 2,000 calorie diet.</p>
        </div>
        <table class="nutrition-table">
          <tr><td><b>Total Fat</b> 22g</td><td>34%</td></tr>
          <tr><td>Saturated Fat 7g</td><td>35%</td></tr>
          <tr><td>Trans Fat 1g</td><td></td></tr>
          <tr><td><b>Cholesterol</b> 115mg</td><td>38%</td></tr>
          <tr><td><b>Sodium</b> 720mg</td><td>30%</td></tr>
          <tr><td><b>Total Carbohydrate</b> 31g</td><td>10%</td></tr>
          <tr><td>Dietary Fiber 2g</td><td>8%</td></tr>
          <tr><td>Sugars 6g</td><td></td></tr>
          <tr><td><b>Protein</b> 40g</td><td></td></tr>
        </table>
      </div>

      <div class="ingredients">
        <h4>INGREDIENTS</h4>
        <p>BEEF BURGERS</p>
        <p>CHOPPED WHITE ONION</p>
        <p>CHEESE</p>
        <p>KETCHUP</p>
        <p>BURGER SAUCE</p>
        <p>LETTUCE LEAF</p>
        <p>1-2 SLICES OF TOMATO</p>
      </div>

      <div class="maker-lines">
        <p>PRODUCED BY:</p>
        <p>DISTRIBUTED BY:</p>
      </div>
    </div>
  </section>

  <!-- Front -->
  <section class="panel front wood">
    <div class="ribbon">
      <div class="ribbon-frame"></div>
      <div class="ribbon-seal"></div>
    </div>

    <div class="front-brand">
      <div class="brand-name"><span class="brand-dot"></span>CRUMBVALE</div>
      <div class="brand-tag">Crust <span class="sep">•</span> Drums <span class="sep">•</span> Melts</div>
    </div>

    <div class="burger-photo" role="img" aria-label="Photo of a sesame bun beef burger with bacon, cheese, tomato and lettuce"></div>

    <div class="product-title">
      <div class="premium-banner">PREMIUM</div>
      <div class="product-beef">BEEF</div>
      <div class="product-burgers">BURGERS</div>
    </div>

    <div class="chalk-rule"></div>
    <div class="contact">
      <span class="contact-dot"></span>
      <span class="contact-dot"></span>
      <svg class="contact-globe" viewBox="0 0 18 18" aria-hidden="true">
        <circle cx="9" cy="9" r="9" fill="#f39122"/>
        <g fill="none" stroke="#2a2a2a" stroke-width="1.1">
          <circle cx="9" cy="9" r="5.5"/>
          <ellipse cx="9" cy="9" rx="2.4" ry="5.5"/>
          <line x1="3.5" y1="9" x2="14.5" y2="9"/>
        </g>
      </svg>
      <span class="contact-url">crumbvale.ca</span>
    </div>
  </section>

  <!-- Ends -->
  <section class="panel end end-left">
    <div class="end-title">
      <div class="premium-banner">PREMIUM</div>
      <div class="product-beef">BEEF</div>
      <div class="product-burgers">BURGERS</div>
    </div>
    <div class="end-brand">
      <div class="brand-name">CRUMBVALE</div>
      <div class="brand-tag">Crust • Drums • Melts</div>
    </div>
  </section>

  <section class="panel end end-right">
    <div class="end-title">
      <div class="premium-banner">PREMIUM</div>
      <div class="product-beef">BEEF</div>
      <div class="product-burgers">BURGERS</div>
    </div>
    <div class="end-brand">
      <div class="brand-name">CRUMBVALE</div>
      <div class="brand-tag">Crust • Drums • Melts</div>
    </div>
  </section>

</body>
</html>
```